Wedding Planning and Event Planners website

I am driven by perfection of my occupation and i look forward to having an attractive and contemporary website for an event and wedding planning group. We are located in the United States and Canada and we offer our services only in these two countries. My website is for people who are planning events such Church programs, weddings, musical concerts, Picnic, etc. My website should have imaginary of events such as weddings, musical concerts and picnic, etc.. I don't have any reference website because i want all designers to be creative and unique. I prefer blue,red,green,yellow colors.

Industry/Entity Type

Wedding

Coding

Coded - Design and coding required

```html
<!DOCTYPE html>
<html lang="en">
<head>
<meta charset="utf-8">
<title>Marlowe Planners — Wedding &amp; Event Planning</title>
<link rel="stylesheet" href="https://fonts.googleapis.com/css2?family=Roboto+Slab:wght@300;400&family=Open+Sans:wght@400;600&family=Montserrat:wght@400;500&display=swap">
<style>
  :root {
    --white: #ffffff;
    --yellow: #f9c80e;
    --yellow-deep: #f5c400;
    --red: #ee1c1c;
    --red-text: #d80f0f;
    --blue: #1a5ed8;
    --blue-deep: #0c3fb0;
    --grey-text: #8a8a8a;
    --dark-text: #444444;
    --hero-a: #3a1a5c;
    --hero-b: #9b3fd6;
    --hero-c: #e57ee0;
  }
  * { box-sizing: border-box; margin: 0; padding: 0; }
  html, body { width: 802px; height: 1200px; overflow: hidden; background: var(--white); }
  body { position: relative; font-family: "Open Sans", sans-serif; }

  .hero {
    position: absolute; left: 0; top: 0; width: 802px; height: 382px;
    background: radial-gradient(ellipse at 50% 45%, var(--hero-c) 0%, var(--hero-b) 45%, var(--hero-a) 100%);
  }
  .brand {
    position: absolute; left: 100px; top: 22px;
    font-family: "Roboto Slab", serif; font-weight: 300; font-size: 22px;
    color: var(--white); letter-spacing: 0.5px;
  }
  .main-nav { position: absolute; top: 33px; left: 353px; display: flex; gap: 0; }
  .main-nav a {
    position: absolute; font-family: "Montserrat", sans-serif; font-size: 9.5px;
    color: var(--white); text-decoration: none; white-space: nowrap;
  }
  .main-nav a.is-active { color: var(--yellow); }
  .hero-title {
    position: absolute; left: 0; top: 166px; width: 802px; text-align: center;
    font-family: "Roboto Slab", serif; font-size: 30px; line-height: 29px;
    color: var(--white); letter-spacing: 0.5px;
  }
  .btn-book {
    position: absolute; left: 354px; top: 238px; width: 96px; height: 25px;
    border-radius: 13px; background: var(--yellow); color: var(--white);
    font-family: "Montserrat", sans-serif; font-size: 11px; line-height: 25px; text-align: center;
  }
  .slider-dots { position: absolute; left: 372px; top: 356px; display: flex; gap: 3px; }
  .slider-dots span { width: 11px; height: 11px; border-radius: 50%; background: var(--white); }
  .slider-dots span.is-current { background: transparent; border: 1.5px solid var(--white); }

  .service { position: absolute; top: 404px; width: 150px; text-align: center; }
  .service svg { display: block; margin: 0 auto; }
  .service h3 {
    font-family: "Roboto Slab", serif; font-weight: 400; font-size: 12.5px;
    color: var(--red-text); margin-top: 2px;
  }
  .service p { font-size: 7px; line-height: 12.5px; color: var(--grey-text); margin-top: 6px; }
  .btn-read {
    display: block; margin: 6px auto 0; width: 69px; height: 19px; background: var(--yellow);
    color: var(--white); font-size: 7px; font-weight: 600; line-height: 19px;
  }

  .welcome { position: absolute; left: 0; top: 588px; width: 802px; height: 304px; }
  .welcome-text { position: absolute; left: 0; top: 86px; width: 802px; text-align: center; color: var(--white); }
  .welcome-text h2 { font-family: "Roboto Slab", serif; font-weight: 300; font-size: 21px; }
  .welcome-text .lead { font-size: 9.5px; margin-top: 11px; }
  .welcome-text .body { font-size: 8.5px; line-height: 15.5px; width: 540px; margin: 10px auto 0; }
  .btn-outline {
    position: absolute; left: 352px; top: 206px; width: 98px; height: 28px;
    border: 1.5px solid var(--white); border-radius: 14px; color: var(--white);
    font-family: "Montserrat", sans-serif; font-size: 11px; line-height: 25px; text-align: center;
  }

  .gallery-title {
    position: absolute; left: 0; top: 886px; width: 802px; text-align: center;
    font-family: "Roboto Slab", serif; font-weight: 300; font-size: 15px; color: var(--dark-text);
  }
  .gallery-title::before, .gallery-title::after {
    content: ""; display: inline-block; width: 30px; height: 1px; background: #bbbbbb;
    vertical-align: middle; margin: 0 6px;
  }
  .thumb {
    position: absolute; top: 928px; width: 141px; height: 98px;
    border: 1px solid #dddddd; padding: 3px; background: var(--white);
  }
  .thumb div { width: 100%; height: 100%; }
  .btn-more {
    position: absolute; left: 360px; top: 1043px; width: 82px; height: 23px;
    border: 1px solid #aaaaaa; border-radius: 12px; color: #777777;
    font-family: "Roboto Slab", serif; font-size: 7.5px; line-height: 21px; text-align: center;
  }

  .site-footer { position: absolute; left: 0; top: 1108px; width: 802px; height: 92px; background: var(--yellow-deep); }
  .footer-nav { position: absolute; left: 105px; top: 34px; }
  .footer-nav a { position: absolute; font-size: 9.5px; color: var(--white); text-decoration: none; white-space: nowrap; }
  .copyright { position: absolute; left: 105px; top: 54px; font-size: 7.5px; color: var(--white); white-space: nowrap; }
  .social { position: absolute; left: 572px; top: 35px; display: flex; gap: 6.5px; }
  .social span { width: 21px; height: 21px; border-radius: 50%; background: var(--white); }
</style>
</head>
<body>

<header class="hero" role="img" aria-label="Candlelit banquet table with glassware in purple light">
  <div class="brand">Marlowe Planners</div>
  <nav class="main-nav">
    <a class="is-active" style="left:0">HOME</a>
    <a style="left:53px">ABOUT</a>
    <a style="left:110px">SERVICES</a>
    <a style="left:181px">GALLERY</a>
    <a style="left:248px">PRICE</a>
    <a style="left:299px">CONTACT</a>
  </nav>
  <h1 class="hero-title">WEDDING &amp; EVENT PLANNING<br>IN US &amp; CANADA</h1>
  <div class="btn-book">Book Now</div>
  <div class="slider-dots"><span class="is-current"></span><span></span><span></span><span></span></div>
</header>

<section class="services">
  <div class="service" style="left:99px">
    <svg width="70" height="96" viewBox="0 0 70 96"><path d="M35 96 C28 74 1 60 1 35 A34 34 0 0 1 69 35 C69 60 42 74 35 96Z" fill="var(--red)"/>
      <rect x="22" y="24" width="26" height="22" rx="3" fill="none" stroke="#fff" stroke-width="2.5"/><line x1="22" y1="30" x2="48" y2="30" stroke="#fff" stroke-width="2.5"/><line x1="28" y1="20" x2="28" y2="26" stroke="#fff" stroke-width="2.5"/><line x1="42" y1="20" x2="42" y2="26" stroke="#fff" stroke-width="2.5"/><path d="M35 43 l-5-5 a3 3 0 0 1 5-3 a3 3 0 0 1 5 3z" fill="#fff"/></svg>
    <h3>Wedding Planning</h3>
    <p>Praesent elementum elit at tellus<br>Curabitur metus luctus eu</p>
    <span class="btn-read">READ MORE</span>
  </div>
  <div class="service" style="left:249px">
    <svg width="70" height="96" viewBox="0 0 70 96"><path d="M35 96 C28 74 1 60 1 35 A34 34 0 0 1 69 35 C69 60 42 74 35 96Z" fill="var(--red)"/>
      <path d="M23 48 V32 L35 22 L47 32 V48 Z" fill="none" stroke="#fff" stroke-width="2.2"/><line x1="35" y1="12" x2="35" y2="22" stroke="#fff" stroke-width="2"/><line x1="31" y1="15" x2="39" y2="15" stroke="#fff" stroke-width="2"/><rect x="32" y="39" width="6" height="9" fill="#fff"/></svg>
    <h3>Church Programs</h3>
    <p>Praesent elementum elit at tellus<br>Curabitur metus luctus eu</p>
    <span class="btn-read">READ MORE</span>
  </div>
  <div class="service" style="left:399px">
    <svg width="70" height="96" viewBox="0 0 70 96"><path d="M35 96 C28 74 1 60 1 35 A34 34 0 0 1 69 35 C69 60 42 74 35 96Z" fill="var(--red)"/>
      <rect x="22" y="30" width="3" height="20" fill="#fff"/><circle cx="23.5" cy="28" r="3" fill="#fff"/><rect x="33" y="30" width="12" height="20" rx="2" fill="#fff"/><line x1="30" y1="40" x2="52" y2="32" stroke="#fff" stroke-width="3"/></svg>
    <h3>Music Concerts</h3>
    <p>Praesent elementum elit at tellus<br>Curabitur metus luctus eu</p>
    <span class="btn-read">READ MORE</span>
  </div>
  <div class="service" style="left:550px">
    <svg width="70" height="96" viewBox="0 0 70 96"><path d="M35 96 C28 74 1 60 1 35 A34 34 0 0 1 69 35 C69 60 42 74 35 96Z" fill="var(--red)"/>
      <path d="M25 22 l-5 10 h10z M35 20 l-5 10 h10z M45 22 l-5 10 h10z" fill="#fff"/><rect x="18" y="36" width="34" height="3" fill="#fff"/><rect x="20" y="42" width="30" height="3" fill="#fff"/><line x1="24" y1="36" x2="20" y2="52" stroke="#fff" stroke-width="2.5"/><line x1="46" y1="36" x2="50" y2="52" stroke="#fff" stroke-width="2.5"/></svg>
    <h3>Picnic &amp; Events</h3>
    <p>Praesent elementum elit at tellus<br>Curabitur metus luctus eu</p>
    <span class="btn-read">READ MORE</span>
  </div>
</section>

<section class="welcome">
  <svg width="802" height="304" viewBox="0 0 802 304" role="img" aria-label="Reception hall under a draped white tent, tinted blue">
    <defs><linearGradient id="welcomeTint" x1="0" y1="0" x2="0" y2="1"><stop offset="0" stop-color="#2a6ee6"/><stop offset="1" stop-color="#0d46c0"/></linearGradient></defs>
    <path d="M0 6 C120 -4 250 2 360 26 C380 28 390 20 400 8 C412 22 420 28 440 26 C560 4 700 -2 802 12 V268 C700 238 560 232 400 236 C240 240 110 262 0 300 Z" fill="url(#welcomeTint)"/>
  </svg>
  <div class="welcome-text">
    <h2>Welcome to Marlowe Planners</h2>
    <p class="lead">At justo id velit placerat molestie Donec dictum lectus non odio Cras a ante vitae enim</p>
    <p class="body">Pellentesque habitant morbi tristique senectus et netus et malesuada fames ac turpis egestas Cras id elit Integer quis urna Ut ante enim dapibus malesuada fringilla eu condimentum quis Donec convallis pede venenatis nibh Duis quam Nam eget lacus Aliquam erat volutpat Quisque dignissim congue leo Mauris vel lacus</p>
  </div>
  <div class="btn-outline">Read More</div>
</section>

<h2 class="gallery-title">OUR GALLERY</h2>
<div class="thumb" style="left:103px"><div role="img" aria-label="Beach wedding aisle with flower petals" style="background:linear-gradient(180deg,#7fc6e8 0%,#e8e0cc 50%,#b0429c 100%)"></div></div>
<div class="thumb" style="left:254px"><div role="img" aria-label="Outdoor reception with white chairs and thatched umbrellas" style="background:linear-gradient(180deg,#e6e6e6 0%,#b89a78 35%,#efefef 100%)"></div></div>
<div class="thumb" style="left:404px"><div role="img" aria-label="Garden ceremony arch with red carpet aisle" style="background:linear-gradient(180deg,#5f9a3a 0%,#e8e8e8 50%,#4f8a2f 100%)"></div></div>
<div class="thumb" style="left:554px"><div role="img" aria-label="Concert stage with purple lights and crowd" style="background:linear-gradient(180deg,#2a1a66 0%,#a23fd6 50%,#120b2a 100%)"></div></div>
<div class="btn-more">VIEW MORE</div>

<footer class="site-footer">
  <nav class="footer-nav">
    <a style="left:0">HOME</a>
    <a style="left:53px">ABOUT</a>
    <a style="left:110px">SERVICES</a>
    <a style="left:181px">GALLERY</a>
    <a style="left:247px">PRICE</a>
    <a style="left:299px">CONTACT</a>
  </nav>
  <p class="copyright">© 2016 Company Name &nbsp;All right reserved &nbsp;Term of Use</p>
  <div class="social"><span></span><span></span><span></span><span></span><span></span></div>
</footer>

</body>
</html>
```